Business Card Design Project : Ridgeline Press

In preparation for market launch, Tamarind's Ridgeline Press require the development of a business card. Ridgeline Press is a Community online publishing web portal. We provide the the city of Whistler located in B.C. (Canada) business directories, News, Classified ads, News, Events and blogs etc.

The main focus of the brand is to help local businesses to corporate with their online advertisement and marketing. Meeting our clients face to face is a must (B2B).

Target Market(s)

The target market is B2B customers. Business Owners to Marketing, advertising Managers

Industry/Entity Type

Business

Requirements
Must have
• - The business card will be two sided.
the BACK side will have our logo which consist of (icon, url,slogan) submited. The logo will be middle and centred.

The FRONT side should have company details:

Company Legal Name: TAMARIND RIDGELINE MEDIA

Owen Farsk
Director of Sales & Marketing

www.tamarindridgeline.biz
owen@tamarindridgeline.biz

Phone: 604 317 8842
#2714 - 582 E. Halvern St.
Vancouver, B.C. V7K2R4 Canada
Nice to have
• - For the "FRONT" side of our business card. You can separate or re-arrange with our logo components (icon, logo,slogan). It does not have to be together.

Also our company legal name is rather long so arrange or organize the name in a way to make it shorter. Your experience and creativity will have to come in play.
Should not have
• should not have other colors beside logo color and black text (2 colors). Also nothing Three dimensional

```html
<!DOCTYPE html>
<html lang="en">
<head>
<meta charset="utf-8">
<title>Ridgeline Press – Business Card</title>
<link rel="stylesheet" href="https://fonts.googleapis.com/css2?family=Source+Sans+3:ital,wght@0,400;0,600;0,700;1,400&display=swap">
<style>
  :root {
    --brand-blue: #338cf4;
    --ink: #111111;
    --paper: #ffffff;
    --backdrop: #070909;
    --card-edge: #c9c9c9;
  }
  * { margin: 0; padding: 0; box-sizing: border-box; }
  html, body {
    width: 1200px; height: 900px; overflow: hidden;
    background: var(--backdrop);
    font-family: "Source Sans 3", "Myriad Pro", Arial, sans-serif;
  }
  .canvas { position: relative; width: 1200px; height: 900px; }

  .card {
    position: absolute;
    background: var(--paper);
    border: 1px solid var(--card-edge);
  }
  .card--front { left: 133px; top: 123px; width: 549px; height: 313px; }
  .card--back  { left: 480px; top: 439px; width: 552px; height: 315px; }

  /* Front */
  .company-name {
    position: absolute;
    right: 387px; top: 101px;
    text-align: right;
    color: var(--brand-blue);
    font-weight: 700;
    font-size: 23px;
    line-height: 21px;
    letter-spacing: -0.2px;
  }
  .contact-band {
    position: absolute;
    left: 165px; top: 88px;
    width: 386px; height: 137px;
    background: var(--brand-blue);
    color: var(--paper);
    padding: 13px 0 0 8px;
  }
  .contact-band__name {
    font-size: 24px; font-weight: 600; line-height: 26px;
  }
  .contact-band__title {
    font-size: 15.5px; font-style: italic; line-height: 19px;
  }
  .contact-band__web {
    font-size: 13.5px; line-height: 18px; margin-top: 2px;
  }
  .contact-line {
    display: flex; align-items: center; gap: 8px;
    font-size: 13.5px; line-height: 20px;
  }
  .contact-line:first-of-type { margin-top: 4px; }
  .contact-line svg { width: 17px; height: 13px; flex: none; }

  /* Back */
  .brand-lockup {
    position: absolute; left: 0; right: 0; top: 96px;
    display: flex; flex-direction: column; align-items: center;
  }
  .brand-lockup__dot {
    width: 66px; height: 66px; border-radius: 50%;
    background: var(--brand-blue);
    margin-bottom: 14px;
  }
  .brand-lockup__url {
    color: var(--ink);
    font-weight: 700; font-size: 24px; line-height: 26px;
    letter-spacing: -0.3px;
  }
  .brand-lockup__slogan {
    color: var(--brand-blue);
    font-size: 17px; line-height: 20px;
  }
</style>
</head>
<body>
<main class="canvas">

  <section class="card card--front" aria-label="Business card front">
    <div class="company-name">TAMARIND<br>RIDGELINE<br>MEDIA</div>
    <div class="contact-band">
      <div class="contact-band__name">Owen Farsk</div>
      <div class="contact-band__title">Director of Sales &amp; Marketing</div>
      <div class="contact-band__web">www.tamarindridgeline.biz / owen@tamarindridgeline.biz</div>
      <div class="contact-line">
        <svg viewBox="0 0 17 13" aria-hidden="true">
          <path d="M1 4 Q8.5 -1 16 4 L14 6 L11.5 4.5 L5.5 4.5 L3 6 Z" fill="#fff"/>
          <rect x="3.5" y="6" width="10" height="6.5" rx="1.5" fill="#fff"/>
          <circle cx="8.5" cy="9.2" r="1.8" fill="#338cf4"/>
        </svg>
        <span>604 317 8842</span>
      </div>
      <div class="contact-line">
        <svg viewBox="0 0 17 13" aria-hidden="true">
          <rect x="1" y="1" width="15" height="11" fill="none" stroke="#fff" stroke-width="1.6"/>
          <path d="M1 1 L8.5 7 L16 1 M1 12 L6.5 6 M16 12 L10.5 6" fill="none" stroke="#fff" stroke-width="1.4"/>
        </svg>
        <span>#2714 - 582 E. Halvern St. Vancouver, B.C. V7K2R4 Canada</span>
      </div>
    </div>
  </section>

  <section class="card card--back" aria-label="Business card back">
    <div class="brand-lockup">
      <div class="brand-lockup__dot"></div>
      <div class="brand-lockup__url">www.tamarindridgeline.biz</div>
      <div class="brand-lockup__slogan">Your neighbourhood guide</div>
    </div>
  </section>

</main>
</body>
</html>
```